Silver Kite Venture Series Travel Brochure

I'm looking for a brochure design for a new travel product - Silver Kite Venture Series, catering for students above 12 years old. Target audience are schools that do destination projects. Brochure to be read by head teacher, parents and students.

Brochure should be A4 in size, 4-6 pages. Format of brochure is hard cover (a folder) with inlet for flyers. Flyers for destinations will be updated from time to time.

Finished job needs to be converted to electronic format for website and email proposal usage.

Attached is text to be used on brochure. Order of section can be adjusted.

For "Elements of the trip", please understand the contents and explain/display it in a graphic form.

For flyer, please come out with a template that I can use for other destinations. The main elements - what's included, number of days, location for pictures, itinerary, educational focus, should be alterable. Attached are text for two sample destinations.
Also attached (tour itinerary example) a version of flyer that I like.

I'm attaching some pictures here. If you find more suitable pictures, please feel free to use them.

Reason: I'm extending the deadline of this project by 4 days, as I need to add details & photo of another travel specialist in personnel session (total of 3 members). Also, in view of the amount of work a designer has to do for this project, I'm giving you more time for submission. Please do not hesitate to be in touch should you need more than 4 days extension. Thank you.

Target Market(s)

Schools - especially the head teacher and parents, to send students above 12 years old to travel

Industry/Entity Type

Electronic

Requirements
Must have
• This is a travel brochure with education elements in it. Parents feel better when their children are travelling for a purpose and lead by responsible teachers/adults whom they can trust. So, the design has to emphasis that education elements and safety are our utmost priority.
Nice to have
• We specialise in environmental study. So, it is nice to have the environmental touch in the design.
Should not have
• Our target market segment is the Middle East, which can be quite sensitive to religion. I prefer not to have any religious related illustration on the design.

```html
<!DOCTYPE html>
<html lang="en">
<head>
<meta charset="utf-8">
<title>Silver Kite Venture Series – Destination Flyer</title>
<link href="https://fonts.googleapis.com/css2?family=Alfa+Slab+One&family=PT+Sans:wght@400;700&display=swap" rel="stylesheet">
<style>
  :root{
    --canvas:#e9ecef;
    --paper:#ffffff;
    --panel-green:#9be31c;
    --stem-green:#6cc40a;
    --sky-blue:#66c4f5;
    --navy:#1c3a8c;
    --ink:#1d1d1b;
    --white:#ffffff;
    --heading-green:#72c814;
  }
  *{margin:0;padding:0;box-sizing:border-box}
  html,body{width:864px;height:1200px;overflow:hidden;background:var(--canvas)}
  body{font-family:"PT Sans",Arial,sans-serif;color:var(--ink);position:relative}
  .page{position:absolute;left:27px;top:24px;width:810px;height:1153px;background:var(--paper);box-shadow:0 2px 10px rgba(0,0,0,.35)}

  .brand{position:absolute;left:42px;top:48px;display:flex;align-items:center;gap:8px}
  .brand-mark{width:16px;height:16px;background:var(--navy)}
  .brand-name{font-weight:700;font-size:16px;color:var(--navy);letter-spacing:.3px}
  .intro{position:absolute;left:270px;top:40px;width:505px;font-size:10px;line-height:12.5px}

  .destination{position:absolute;left:0;width:810px;height:500px}
  .dest-7{top:108px}
  .dest-8{top:636px}

  .photo{position:absolute;left:39px;top:0;width:239px;height:476px}
  .dest-7 .photo{background:linear-gradient(180deg,#9fb4c9 0%,#b98a5c 20%,#a26f45 36%,#4f7a2e 52%,#6fb0a8 74%,#3f8f5a 100%)}
  .dest-8 .photo{background:linear-gradient(160deg,#7a8a4a 0%,#4e5a32 35%,#8c8d84 65%,#556b2f 100%)}
  .dest-title{position:absolute;left:39px;width:239px;text-align:center;color:var(--white);font-family:"Alfa Slab One",Georgia,serif;text-shadow:0 1px 3px rgba(0,0,0,.45)}
  .dest-num{font-size:17px;line-height:20px}
  .dest-name{font-size:38px;line-height:41px}
  .dest-7 .dest-title{top:262px}
  .dest-8 .dest-title{top:276px}

  .stem{position:absolute;left:285px;top:-4px;width:6px;height:462px;background:var(--stem-green);border-radius:3px}

  .itinerary{position:absolute;left:284px;top:0;width:487px;height:236px;background:var(--panel-green);padding:36px 0 0 25px;display:flex}
  .dest-8 .itinerary{height:229px;padding-top:34px}
  .itin-col{font-size:10.5px;line-height:12.5px}
  .itin-col:first-child{width:231px}
  .day{font-family:"Alfa Slab One",Georgia,serif;font-size:11px;line-height:14px;color:var(--white);margin-top:1px}

  .focus{position:absolute;left:284px;top:236px;width:487px;height:161px;background:var(--sky-blue);padding:16px 0 0 25px;display:flex}
  .dest-8 .focus{top:229px;height:154px}
  .focus-col:first-child{width:231px}
  .focus-col:last-child{width:200px}
  .focus h3{font-family:"Alfa Slab One",Georgia,serif;font-weight:400;font-size:16px;line-height:19px;color:var(--navy)}
  .focus p{font-weight:700;font-size:13px;line-height:16px;color:var(--white);margin-bottom:7px}

  .included{position:absolute;left:284px;top:397px;width:487px;padding:8px 0 0 25px}
  .dest-8 .included{top:383px}
  .included h3{font-family:"Alfa Slab One",Georgia,serif;font-weight:400;font-size:16px;line-height:20px;color:var(--heading-green);margin-bottom:6px}
  .included-list{display:flex;font-size:10.5px;line-height:13.5px}
  .included-list ul{list-style:none}
  .included-list ul:first-child{width:231px}
</style>
</head>
<body>
<div class="page">
  <div class="brand"><span class="brand-mark"></span><span class="brand-name">Northgate Advisory</span></div>
  <p class="intro">Above are some of our more popular destinations. With our vast knowledge and expertise in the Middle East, Asia and Europe destinations, we are able to cater for other countries not mentioned. We are constantly expanding our radar to new destinations. Upcoming destinations are Vietnam, Cambodia and Namibia.</p>

  <section class="destination dest-7">
    <div class="photo" role="img" aria-label="Desert oasis with rocky cliffs, palm trees and a clear pool"></div>
    <div class="dest-title"><div class="dest-num">Destination 7</div><div class="dest-name">JORDAN<br>&amp;<br>OMAN</div></div>
    <div class="itinerary">
      <div class="itin-col">
        <div class="day">Day 1</div>Arrival at Kota Kinabalu<br>Cultural performance dinner
        <div class="day">Day 2</div>Kiulu river rafting<br>Village visit
        <div class="day">Day 3</div>Kinabalu Park trekking<br>Poring Hot Spring visit
        <div class="day">Day 4</div>Sabah tea visit<br>Sukau Kinabatangan wildlife cruise
      </div>
      <div class="itin-col">
        <div class="day">Day 5</div>Sepilok Orang Utan Rehabilitation<br>Center visit<br>Sandakan city tour
        <div class="day">Day 6</div>Fly to Kuala Lumpur<br>City tour<br>School visit (optional)
        <div class="day">Day 7</div>Departure
      </div>
    </div>
    <div class="focus">
      <div class="focus-col">
        <h3>Main focus subject</h3><p>Environmental Management</p>
        <h3>Related subjects</h3><p>Geography, Development<br>Studies, Agriculture,<br>Physical Education</p>
      </div>
      <div class="focus-col">
        <h3>Environmental focus</h3><p>Biodiversity of Malaysian<br>rainforests and conservation<br>projects.</p>
      </div>
    </div>
    <div class="included">
      <h3>What's included in price:</h3>
      <div class="included-list">
        <ul><li>Air ticket</li><li>All accommodation</li><li>Full time tour director</li></ul>
        <ul><li>Meals</li><li>Tours led by local expert tour guides</li><li>Entrance fees to attractions</li></ul>
      </div>
    </div>
    <div class="stem" aria-hidden="true"></div>
  </section>

  <section class="destination dest-8">
    <div class="photo" role="img" aria-label="Giant panda resting on mossy rocks among greenery"></div>
    <div class="dest-title"><div class="dest-num">Destination 8</div><div class="dest-name">CHINA</div></div>
    <div class="itinerary">
      <div class="itin-col">
        <div class="day">Day 1</div>Arrival at Athens<br>Athens city tour
        <div class="day">Day 2</div>Athens to Mykonos on cruise<br>Mykonos tour
        <div class="day">Day 3</div>Mykonos to Kusadasi (Turkey) on cruise<br>Kusadasi tour
        <div class="day">Day 4</div>Kusadasi to Santorini on cruise<br>Santorini and volcano tour
      </div>
      <div class="itin-col">
        <div class="day">Day 5</div>Santorini to Athens on cruise<br>Athens second city tour
        <div class="day">Day 6</div>Athens to Delphi by coach (2 hours)<br>Visit hill towns on way<br>Delphi tour
        <div class="day">Day 7</div>Departure
      </div>
    </div>
    <div class="focus">
      <div class="focus-col">
        <h3>Main focus subject</h3><p>Geography</p>
        <h3>Related subjects</h3><p>History, Anthropology,<br>Environmental Management,<br>Art and Design</p>
      </div>
      <div class="focus-col">
        <h3>Environmental focus</h3><p>Marine ecology and related<br>human threats.</p>
      </div>
    </div>
    <div class="included">
      <h3>What's included in price:</h3>
      <div class="included-list">
        <ul><li>Air ticket</li><li>All accommodation</li><li>Full time tour director</li></ul>
        <ul><li>Meals</li><li>Tours led by local expert tour guides</li><li>Entrance fees to attractions</li></ul>
      </div>
    </div>
    <div class="stem" aria-hidden="true"></div>
  </section>
</div>
</body>
</html>
```